zENTRO Flight Simulator ad

We are looking to create a new ad, it should be a small ad about 59x47mm (SORRY POSTED WRONG SIZE INITIALLY) , but adaptable in size as some magazines have slightly different sizes
it should work in colour and black and white as well as black, white and red.

it should feature a pilot or cockpit ( i like the idea and stye of this for example)
http://www.brovendale-example.com/sim%20choice/harvest%2013.jpg

Message: Make someone you love a Pilot this Christmas

and then logo zENTRO (with slogan FLIGHT SIMULATOR EXPERIENCE) and website www.gozentro.co.uk
Our design manual can be viewed here
https://www.filecrate-example.com/s/qmx8wtrlkzpvbnd/zentro_manual_EN_HQ%20copy.pdf

our website is www.gozentro.co.uk

Look forward to great ideas and designs :)

Brett

i have updated the correct size, i am very sorry for the inconvenience, must  be the jetlag :(

Brett

eb1f27

```html
<!DOCTYPE html>
<html lang="en">
<head>
<meta charset="utf-8">
<title>zENTRO Flight Simulator Experience – Christmas Ad</title>
<link rel="stylesheet" href="https://fonts.googleapis.com/css2?family=Jost:wght@500;600&family=Arimo:wght@700&display=swap">
<style>
  :root {
    --brand-red: #e8323a;
    --frame-white: #ffffff;
    --text-white: #ffffff;
    --stitch-red: #d4232b;
    --photo-cabin-light: #e9edf2;
    --photo-shirt: #d6dce4;
    --photo-panel: #7d8da4;
    --photo-instruments: #3c4d6e;
    --photo-deep: #22304a;
  }
  html, body {
    margin: 0;
    padding: 0;
    overflow: hidden;
  }
  .ad {
    position: relative;
    width: 950px;
    height: 1200px;
    background: var(--brand-red);
    overflow: hidden;
    font-family: "Jost", "Helvetica Neue", Arial, sans-serif;
    color: var(--text-white);
  }
  .brand {
    position: absolute;
    left: 46px;
    top: 84px;
  }
  .brand-name {
    margin: 0;
    font-size: 76px;
    font-weight: 500;
    line-height: 1;
    letter-spacing: -1.5px;
  }
  .brand-tagline {
    margin: 10px 0 0 3px;
    font-size: 14.5px;
    font-weight: 600;
    letter-spacing: -0.3px;
    text-transform: uppercase;
  }
  .website {
    position: absolute;
    right: 50px;
    top: 42px;
    font-family: "Arimo", Arial, sans-serif;
    font-weight: 700;
    font-size: 22px;
    color: var(--text-white);
    text-decoration: none;
  }
  .heart-photo {
    position: absolute;
    left: 0;
    top: 0;
  }
  .headline {
    position: absolute;
    left: 40px;
    top: 804px;
    width: 460px;
    margin: 0;
    text-align: center;
    font-size: 66px;
    font-weight: 600;
    line-height: 77px;
    letter-spacing: -0.8px;
  }
</style>
</head>
<body>
  <main class="ad">
    <header class="brand">
      <h1 class="brand-name">zENTRO</h1>
      <p class="brand-tagline">Flight Simulator Experience</p>
    </header>

    <a class="website" href="http://www.gozentro.co.uk">www.gozentro.co.uk</a>

    <svg class="heart-photo" width="950" height="1200" viewBox="0 0 950 1200">
      <defs>
        <linearGradient id="cockpit-tones" x1="0.05" y1="0.1" x2="1" y2="0.85">
          <stop offset="0" stop-color="var(--photo-cabin-light)"/>
          <stop offset="0.35" stop-color="var(--photo-shirt)"/>
          <stop offset="0.6" stop-color="var(--photo-panel)"/>
          <stop offset="0.82" stop-color="var(--photo-instruments)"/>
          <stop offset="1" stop-color="var(--photo-deep)"/>
        </linearGradient>
      </defs>
      <path class="heart-frame"
            d="M693,382 C655,300 575,245 485,255 C390,266 318,340 316,430 C314,540 390,620 462,705 C525,780 580,870 611,958 C690,880 800,795 890,720 C950,670 1000,610 1012,520 C1025,420 965,300 865,298 C795,296 725,330 693,382 Z"
            fill="url(#cockpit-tones)" stroke="var(--frame-white)" stroke-width="18"
            role="img" aria-label="Photo of a smiling pilot in a Santa hat and white uniform shirt sitting at the controls of a flight simulator cockpit"/>
      <path class="heart-stitch"
            d="M693,382 C655,300 575,245 485,255 C390,266 318,340 316,430 C314,540 390,620 462,705 C525,780 580,870 611,958 C690,880 800,795 890,720 C950,670 1000,610 1012,520 C1025,420 965,300 865,298 C795,296 725,330 693,382 Z"
            transform="translate(664 610) scale(0.975) translate(-664 -610)"
            fill="none" stroke="var(--stitch-red)" stroke-width="2" stroke-dasharray="5 4"/>
    </svg>

    <h2 class="headline">Make someone you love a Pilot this Christmas</h2>
  </main>
</body>
</html>
```